WordPress website design for wealth management company

A modern clean look website for a service company. This is mostly for information only, with a form to capture prospect contact information and schedule a 15 minutes call. There will be several static pages describe what services we offer, how we are different, and a blog section for posting articles and share resources. A section for client testimonials.
I want a website that is easy to understand and maintain. No proprietary plugins that cost extra. The main thing I need help is the visual layout / color palette that present a clean and professional look, select the suitable stock photos that convey the image of trust, professional, innovative, and high service.
Some websites with style I like include the following
- https://www.halvorbrook.com/
- https://www.trivanplanningworks.com/
- https://morvellfunds.com/private-equity-partners/
Also some websites in other industries with clean modern look
- https://zentrell.com/
- https://quovra.com/
- https://www.plumtorvik.com/
I want the end product to be a fully functional website that I can upload into web hosting service I use and I can easily add content and maintain myself in the future.

```html
<!DOCTYPE html>
<html lang="en">
<head>
<meta charset="utf-8">
<title>Brantley Wealth</title>
<link href="https://fonts.googleapis.com/css2?family=Montserrat:wght@700;800&family=Roboto:wght@400;500;700&display=swap" rel="stylesheet">
<style>
:root{
  --purple:#4b1f86;
  --purple-soft:#6a3fb0;
  --yellow:#f9b82c;
  --ink:#111111;
  --text:#3d3d3d;
  --muted:#6e6e6e;
  --light:#f1f1f3;
  --line:#d9d9de;
  --white:#ffffff;
  --black:#000000;
}
*{box-sizing:border-box;margin:0;padding:0}
html,body{width:1200px;height:4800px;overflow:hidden;background:var(--white)}
body{position:relative;font-family:"Roboto",Arial,sans-serif;color:var(--text)}
.abs{position:absolute}
.photo{position:absolute;overflow:hidden}
.section-title{position:absolute;left:0;width:1200px;text-align:center;font-weight:500;font-size:40px;color:var(--ink)}
.title-bar{position:absolute;height:6px;width:112px;background:var(--purple);border-radius:3px;transform:skewX(-30deg)}
.btn{position:absolute;display:flex;align-items:center;justify-content:center;background:var(--yellow);color:var(--ink);font-weight:700;font-size:19px;border-radius:8px}

/* header */
.brand{position:absolute;left:112px;top:14px;width:160px;text-align:center}
.brand-mark{width:54px;height:54px;border-radius:50%;background:var(--purple);margin:0 auto 6px}
.brand-name{font-family:"Montserrat",Arial,sans-serif;font-weight:800;color:var(--purple);font-size:24px;letter-spacing:2px;line-height:1}
.brand-sub{font-family:"Montserrat",Arial,sans-serif;font-weight:800;color:var(--purple);font-size:12px;letter-spacing:3px;margin-top:3px}
.contact{position:absolute;top:26px;display:flex;align-items:center;gap:12px;font-size:16px;color:var(--ink)}
.contact .ico{width:30px;height:30px;border-radius:50%;background:var(--purple);display:flex;align-items:center;justify-content:center}
.nav{position:absolute;top:85px;right:112px;display:flex;gap:33px;font-size:17px;color:var(--ink)}

/* hero */
.hero{left:0;top:128px;width:1200px;height:560px;background:linear-gradient(90deg,#4d83b8 0%,#c9d3dc 30%,#eef0f0 48%,#e5e2dc 62%,#9d9a94 85%,#6f6d6a 100%)}
.hero-fade{position:absolute;left:380px;top:128px;width:440px;height:380px;background:radial-gradient(ellipse at center,rgba(255,255,255,.85),rgba(255,255,255,0) 70%)}
.hero-kicker{position:absolute;top:220px;left:0;width:1200px;text-align:center;font-size:26px;color:var(--ink)}
.hero-title{position:absolute;top:258px;left:0;width:1200px;text-align:center;font-family:"Montserrat",Arial,sans-serif;font-weight:800;font-size:62px;color:var(--purple);letter-spacing:2px}
.hero-sub{position:absolute;top:345px;left:0;width:1200px;text-align:center;font-family:"Montserrat",Arial,sans-serif;font-weight:800;font-size:42px;color:var(--yellow);letter-spacing:3px}

/* about */
.about-text{position:absolute;left:680px;width:415px;font-size:14.5px;line-height:24px;color:var(--muted)}

/* services */
.services-bg{left:0;top:1325px;width:1200px;height:663px;background:linear-gradient(90deg,#e6e8ec,#f4f5f7 40%,#eceef1);border-bottom-left-radius:60px}
.svc-card{position:absolute;top:1474px;width:313px;height:439px;background:var(--white);border:2px solid #b9b9c4}
.svc-card .photo{left:0;top:0;width:309px;height:290px}
.svc-label{position:absolute;left:0;top:244px;width:290px;height:42px;background:var(--yellow);clip-path:polygon(0 0,92% 0,100% 100%,0 100%);display:flex;align-items:center;justify-content:center;font-weight:700;font-size:18px;color:var(--ink)}
.svc-text{position:absolute;left:18px;right:18px;top:318px;text-align:center;font-size:15px;line-height:24px;color:var(--ink)}
.arrow{position:absolute;width:38px;height:38px;border-radius:50%;display:flex;align-items:center;justify-content:center}

/* review */
.review-card{position:absolute;background:var(--white);border:2px solid var(--line);box-shadow:6px 6px 0 #ececf0}
.stars{color:var(--yellow);font-size:25px;letter-spacing:5px}
.dot{position:absolute;top:2427px;width:15px;height:15px;border-radius:50%;background:var(--purple-soft);border:3px solid #c9bde0}

/* blog */
.blog-bg{left:0;top:2530px;width:1200px;height:697px;background:#f3f3f5}
.blog-card{position:absolute;top:2696px;width:316px;height:382px;background:var(--white);box-shadow:0 2px 8px rgba(0,0,0,.12)}
.blog-card .photo{left:4px;top:4px;width:308px;height:257px}
.date{position:absolute;left:0;top:207px;width:192px;height:56px;background:var(--yellow);border-radius:0 14px 14px 0;display:flex;align-items:center;gap:14px;padding-left:16px;color:var(--white);font-weight:700;font-size:20px}
.blog-title{position:absolute;left:22px;top:283px;font-weight:700;font-size:16px;color:var(--ink)}
.blog-text{position:absolute;left:22px;right:22px;top:307px;font-size:15px;line-height:24px;color:var(--muted)}

/* different */
.diff-bg{left:0;top:3227px;width:1200px;height:629px;background:var(--yellow)}
.diff-item{position:absolute;left:128px;display:flex;gap:22px;font-size:17px;line-height:24px;color:var(--ink)}
.diff-ico{width:36px;height:36px;border-radius:50%;background:var(--white);border:4px solid var(--purple);flex:none;margin-top:2px}

/* form */
.field{position:absolute;height:56px;border:2px solid #c4c4cc;border-radius:8px;display:flex;align-items:center;gap:12px;padding-left:36px;font-size:20px;font-weight:500;color:var(--purple)}

/* footer */
.footer{left:0;top:4473px;width:1200px;height:327px;background:var(--black)}
.foot-head{position:absolute;top:4515px;font-size:21px;font-weight:500;color:var(--white)}
.foot-links{position:absolute;top:4569px;list-style:none;font-size:16px;line-height:33px;color:var(--white)}
.social{position:absolute;top:4671px;width:52px;height:52px;border-radius:50%;background:var(--white)}
.copy{position:absolute;top:4762px;left:0;width:1200px;text-align:center;font-size:15px;color:var(--white)}
</style>
</head>
<body>

<!-- header -->
<div class="brand">
  <div class="brand-mark"></div>
  <div class="brand-name">BRANTLEY</div>
  <div class="brand-sub">WEALTH</div>
</div>
<div class="contact" style="left:640px">
  <span class="ico"><svg width="14" height="14" viewBox="0 0 24 24"><path fill="#fff" d="M6.6 10.8a15 15 0 0 0 6.6 6.6l2.2-2.2c.3-.3.7-.4 1-.2 1.1.4 2.3.6 3.6.6.6 0 1 .4 1 1V20c0 .6-.4 1-1 1A17 17 0 0 1 3 4c0-.6.4-1 1-1h3.5c.6 0 1 .4 1 1 0 1.3.2 2.5.6 3.6.1.3 0 .7-.2 1z"/></svg></span>+1 (555) 0142 309
</div>
<div class="contact" style="left:846px">
  <span class="ico"><svg width="14" height="14" viewBox="0 0 24 24"><path fill="#fff" d="M3 5h18v14H3z"/><path d="M3 5l9 7 9-7" stroke="#4b1f86" stroke-width="2" fill="none"/></svg></span>info @ brantleywealth.com
</div>
<nav class="nav"><span>Home</span><span>About Us</span><span>Our Services</span><span>Client Review</span><span>Blog</span><span>Contact us</span></nav>

<!-- hero -->
<div class="photo hero" role="img" aria-label="Caregiver kindly holding the hands of a senior woman"></div>
<div class="hero-fade"></div>
<div class="hero-kicker">Welcome To</div>
<div class="hero-title">BRANTLEY</div>
<div class="hero-sub">WEALTH</div>
<div class="btn" style="left:516px;top:436px;width:150px;height:46px;font-size:18px">Get Started</div>
<svg class="abs" style="left:0;top:676px" width="1200" height="44" viewBox="0 0 1200 44">
  <polygon points="0,16 1200,0 1200,26 0,30" fill="#4b1f86"/>
  <polygon points="0,14 890,14 915,42 0,42" fill="#f9b82c"/>
</svg>

<!-- about -->
<div class="section-title" style="top:765px">About Us</div>
<div class="title-bar" style="left:518px;top:828px"></div>
<svg class="abs" style="left:180px;top:830px" width="420" height="430" viewBox="0 0 420 430">
  <circle cx="215" cy="215" r="205" fill="none" stroke="#ece6f6" stroke-width="10"/>
  <path d="M215 10 A205 205 0 0 1 215 420" fill="none" stroke="#f9b82c" stroke-width="12"/>
</svg>
<div class="photo" style="left:215px;top:850px;width:380px;height:380px;border-radius:50%;background:linear-gradient(135deg,#cfd9e4,#3c8ea6 55%,#1f6f82)" role="img" aria-label="Smiling team of young healthcare workers"></div>
<p class="about-text" style="top:876px">Lorem ipsum dolor sit amet, consectetur adipiscing elit, sed do eiusmod tempor incididunt ut labore et dolore magna aliqua. Ut enim ad minim veniam, quis nostrud exercitation ullamco</p>
<p class="about-text" style="top:1004px">Lorem ipsum dolor sit amet, consectetur adipiscing elit, sed do eiusmod tempor incididunt ut labore et dolore magna aliqua. Ut enim ad minim veniam, quis nostrud exercitation laboris nisi ut aliquip ex ea commodo consequat. Duis aute irure dolor in reprehenderit in voluptate velit esse cillum dolore eu fugiat nulla pariatur.</p>
<div class="btn" style="left:680px;top:1191px;width:151px;height:45px">Read More</div>

<!-- services -->
<div class="photo services-bg" role="img" aria-label="Faint background of doctor and patient consultation"></div>
<div class="section-title" style="top:1355px">what services we offer</div>
<div class="title-bar" style="left:392px;top:1418px"></div>

<div class="svc-card" style="left:112px">
  <div class="photo" style="background:linear-gradient(180deg,#cfe0ef,#8fae7e 70%,#6f8f5c)" role="img" aria-label="Smiling volunteer outdoors"></div>
  <div class="svc-label">Lorum Ipsum</div>
  <p class="svc-text">Lorem ipsum dolor sit amet, consectetur adipiscing elit, sed do eiusmod tempor incididunt ut labore et dolore magna aliqua. Ut enim ad</p>
</div>
<div class="svc-card" style="left:445px">
  <div class="photo" style="background:linear-gradient(180deg,#e4e8ec,#b8c4cf 60%,#6b7c8c)" role="img" aria-label="Doctor reviewing notes with a patient"></div>
  <div class="svc-label">Lorum Ipsum</div>
  <p class="svc-text">Lorem ipsum dolor sit amet, consectetur adipiscing elit, sed do eiusmod tempor incididunt ut labore et dolore magna aliqua. Ut enim ad</p>
</div>
<div class="svc-card" style="left:777px">
  <div class="photo" style="background:linear-gradient(180deg,#eef0ee,#d5d8d2 60%,#9a8a7c)" role="img" aria-label="Doctor greeting a senior patient"></div>
  <div class="svc-label">Lorum Ipsum</div>
  <p class="svc-text">Lorem ipsum dolor sit amet, consectetur adipiscing elit, sed do eiusmod tempor incididunt ut labore et dolore magna aliqua. Ut enim ad</p>
</div>
<div class="arrow" style="left:54px;top:1678px;background:var(--purple)"><svg width="14" height="14" viewBox="0 0 14 14"><path d="M9 2L4 7l5 5" stroke="#fff" stroke-width="2.4" fill="none"/></svg></div>
<div class="arrow" style="left:1126px;top:1678px;background:#d7cdea"><svg width="14" height="14" viewBox="0 0 14 14"><path d="M5 2l5 5-5 5" stroke="#fff" stroke-width="2.4" fill="none"/></svg></div>

<!-- client review -->
<div class="section-title" style="top:2071px">Client Review</div>
<div class="title-bar" style="left:478px;top:2134px"></div>

<div class="review-card" style="left:-20px;top:2189px;width:218px;height:190px">
  <div class="stars abs" style="left:18px;top:24px">★★★★</div>
  <p class="abs" style="left:18px;top:88px;font-size:15px;line-height:24px;color:var(--muted)">sit amet, consectetur<br>do eiusmod tempor</p>
</div>

<div class="review-card" style="left:485px;top:2189px;width:422px;height:190px">
  <div class="abs" style="left:28px;top:26px;font-size:20px;font-weight:500;color:var(--ink)">Lorum Ipsum</div>
  <div class="stars abs" style="left:206px;top:20px">★★★★★</div>
  <p class="abs" style="left:78px;top:86px;width:300px;font-size:15px;line-height:24px;color:var(--muted);text-align:justify">Lorem ipsum dolor sit amet, consectetur adipiscing elit, sed do eiusmod tempor incididunt ut labore.</p>
</div>
<div class="photo" style="left:405px;top:2255px;width:121px;height:124px;background:linear-gradient(160deg,#c9a98c,#5a3c2e)" role="img" aria-label="Portrait of a happy client"></div>

<div class="photo" style="left:1112px;top:2255px;width:88px;height:124px;background:linear-gradient(160deg,#a3b6c8,#4f5f70)" role="img" aria-label="Portrait of a client in business attire"></div>

<div class="dot" style="left:558px"></div>
<div class="dot" style="left:581px;background:var(--yellow);border-color:#f4dd9c"></div>
<div class="dot" style="left:604px"></div>
<div class="dot" style="left:627px"></div>

<!-- blog -->
<div class="photo blog-bg"></div>
<div class="section-title" style="top:2577px">Blog</div>
<div class="title-bar" style="left:565px;top:2640px"></div>

<div class="blog-card" style="left:112px">
  <div class="photo" style="background:linear-gradient(180deg,#d7e6f0,#3b86b9 70%,#2a6e9c)" role="img" aria-label="Medical staff in blue scrubs talking"></div>
  <div class="date"><svg width="24" height="24" viewBox="0 0 24 24"><rect x="3" y="5" width="18" height="16" rx="2" fill="none" stroke="#fff" stroke-width="2"/><path d="M3 10h18M8 3v4M16 3v4" stroke="#fff" stroke-width="2"/></svg>09-09-2023</div>
  <div class="blog-title">Lorem ipsum dolor sit amet</div>
  <p class="blog-text">adipiscing elit, sed do eiusmod tempor incididunt ut labore et dolore magna</p>
</div>
<div class="blog-card" style="left:443px">
  <div class="photo" style="background:linear-gradient(180deg,#3a5e88,#2f4e74 60%,#c7ced7)" role="img" aria-label="Doctors reviewing a tablet together"></div>
  <div class="date"><svg width="24" height="24" viewBox="0 0 24 24"><rect x="3" y="5" width="18" height="16" rx="2" fill="none" stroke="#fff" stroke-width="2"/><path d="M3 10h18M8 3v4M16 3v4" stroke="#fff" stroke-width="2"/></svg>09-09-2023</div>
  <div class="blog-title">Lorem ipsum dolor sit amet</div>
  <p class="blog-text">adipiscing elit, sed do eiusmod tempor incididunt ut labore et dolore magna</p>
</div>
<div class="blog-card" style="left:773px">
  <div class="photo" style="background:linear-gradient(180deg,#eceff1,#cdd3d8 60%,#8c96a0)" role="img" aria-label="Senior doctor smiling in a clinic"></div>
  <div class="date"><svg width="24" height="24" viewBox="0 0 24 24"><rect x="3" y="5" width="18" height="16" rx="2" fill="none" stroke="#fff" stroke-width="2"/><path d="M3 10h18M8 3v4M16 3v4" stroke="#fff" stroke-width="2"/></svg>09-09-2023</div>
  <div class="blog-title">Lorem ipsum dolor sit amet</div>
  <p class="blog-text">adipiscing elit, sed do eiusmod tempor incididunt ut labore et dolore magna</p>
</div>
<div class="btn" style="left:475px;top:3126px;width:252px;height:45px;font-size:18px">See Our Latest News</div>

<!-- how we are different -->
<div class="photo diff-bg"></div>
<div class="section-title" style="top:3297px">How We Are Different</div>
<div class="title-bar" style="left:398px;top:3360px"></div>
<div class="diff-item" style="top:3418px"><span class="diff-ico"></span><p>Lorem ipsum dolor sit amet, consectetur<br>adipiscing elit, sed do eiusmod.</p></div>
<div class="diff-item" style="top:3495px"><span class="diff-ico"></span><p>Lorem ipsum dolor sit amet, consectetur<br>adipiscing elit, sed do eiusmod.</p></div>
<div class="diff-item" style="top:3572px"><span class="diff-ico"></span><p>Lorem ipsum dolor sit amet, consectetur<br>adipiscing elit, sed do eiusmod.</p></div>
<div class="diff-item" style="top:3649px"><span class="diff-ico"></span><p>Lorem ipsum dolor sit amet, consectetur<br>adipiscing elit, sed do eiusmod.</p></div>
<div class="btn" style="left:188px;top:3735px;width:150px;height:45px;background:var(--white)">Read More</div>
<div class="photo" style="left:602px;top:3426px;width:476px;height:316px;background:radial-gradient(circle at 50% 50%,#e7eaee,#9aa3ad 70%,#7d8792)" role="img" aria-label="Hand touching a lean process concept diagram"></div>

<!-- schedule -->
<div class="section-title" style="top:3936px">Schedule A 15 Minutes Call</div>
<div class="title-bar" style="left:342px;top:3999px"></div>
<div class="field" style="left:184px;top:4078px;width:361px"><svg width="18" height="18" viewBox="0 0 24 24"><circle cx="12" cy="7" r="5" fill="#4b1f86"/><path d="M3 22a9 9 0 0 1 18 0z" fill="#4b1f86"/></svg>Name</div>
<div class="field" style="left:656px;top:4078px;width:361px"><svg width="20" height="18" viewBox="0 0 24 20"><rect x="1" y="2" width="22" height="16" rx="2" fill="#4b1f86"/><path d="M1 4l11 8 11-8" stroke="#fff" stroke-width="2" fill="none"/></svg>E Mail</div>
<div class="field" style="left:184px;top:4162px;width:361px"><svg width="18" height="18" viewBox="0 0 24 24"><rect x="1" y="1" width="22" height="22" rx="4" fill="#4b1f86"/><path d="M8 6l2 3-1.5 1.5a8 8 0 0 0 5 5L15 14l3 2-1 2.5C11 18 6 13 5.5 7z" fill="#fff"/></svg>Phone</div>
<div class="field" style="left:656px;top:4162px;width:361px"><svg width="18" height="18" viewBox="0 0 24 24"><path d="M22 2L2 11l9 2 2 9z" fill="#4b1f86"/></svg>Location</div>
<div class="field" style="left:184px;top:4248px;width:833px;height:98px;align-items:flex-start;padding-top:18px"><svg width="20" height="18" viewBox="0 0 24 22"><path d="M12 1C5.5 1 1 5 1 9.5c0 2.5 1.4 4.7 3.6 6.2L3 21l5.6-3.1c1.1.3 2.2.4 3.4.4 6.5 0 11-4 11-8.8S18.5 1 12 1z" fill="#4b1f86"/></svg>Message</div>
<div class="btn" style="left:184px;top:4374px;width:151px;height:45px">Submit</div>

<!-- footer -->
<div class="photo footer"></div>
<div class="foot-head" style="left:119px">Quick Links</div>
<ul class="foot-links" style="left:119px"><li>Home</li><li>About Us</li><li>Our Services</li><li>Client Review</li><li>Blog</li><li>Contact us</li></ul>
<div class="abs" style="left:500px;top:4508px;width:200px;text-align:center">
  <div style="width:56px;height:56px;border-radius:50%;background:var(--white);margin:0 auto 8px"></div>
  <div class="brand-name" style="color:var(--white)">BRANTLEY</div>
  <div class="brand-sub" style="color:var(--white)">WEALTH</div>
</div>
<div class="social" style="left:490px"></div>
<div class="social" style="left:574px"></div>
<div class="social" style="left:660px"></div>
<div class="foot-head" style="left:969px">Other Links</div>
<ul class="foot-links" style="left:969px"><li>FAQ</li><li>Career</li><li>Lorum Ipsum</li><li>Sit Amed</li><li>Dolor</li></ul>
<div class="copy">Copyright 2023 - Brantley Wealth - All Rights Reserved</div>

</body>
</html>
```